Process Serving Company needs a letterhead design

Looking to have a letterhead designed for letters to attorneys advertising our business. We would like something eye catching but professional. Colors and logos are attached. Please add "Process Service and Attorney Support" near the logo or header

Target Market(s)

Attorneys

Font styles to use
Serif
Sans Serif

Colors
33a6d7
0255a3
85cae6
cee9f5
ecf7fb

```html
<!DOCTYPE html>
<html lang="en">
<head>
<meta charset="utf-8">
<title>Mesa Ridge Serve Letterhead</title>
<link href="https://fonts.googleapis.com/css2?family=Lato:wght@400;700&family=Yellowtail&display=swap" rel="stylesheet">
<style>
  :root {
    --backdrop: #e4e4ea;
    --paper: #ffffff;
    --brand-blue: #1a96d4;
    --brand-deep: #0255a3;
    --ink: #4a4a4a;
    --ink-dark: #333333;
    --swoosh: #1e1e1e;
    --divider: #9a9a9a;
  }
  * { box-sizing: border-box; margin: 0; padding: 0; }
  html, body {
    width: 1200px; height: 1200px; overflow: hidden;
    background: var(--backdrop);
  }
  .letterhead {
    position: absolute; left: 197px; top: 30px;
    width: 806px; height: 1140px;
    background: var(--paper);
    box-shadow: 0 4px 18px rgba(0,0,0,0.12);
    font-family: "Lato", sans-serif;
    color: var(--ink);
    overflow: hidden;
  }
  .brand {
    position: absolute; left: 59px; top: 58px;
    display: flex; align-items: center; gap: 12px;
  }
  .brand-mark {
    width: 18px; height: 18px; background: var(--brand-blue);
  }
  .brand-name {
    font-family: "Lato", sans-serif; font-weight: 400;
    font-size: 26px; color: var(--brand-blue); letter-spacing: 0.5px;
  }
  .contact {
    position: absolute; left: 595px; top: 43px;
    border-left: 1.5px solid var(--divider);
    padding-left: 12px;
    list-style: none;
    font-size: 11.5px; color: var(--ink-dark);
  }
  .contact li {
    display: flex; align-items: center; gap: 7px;
    height: 19px;
  }
  .contact svg { width: 11px; height: 11px; fill: var(--brand-blue); flex: none; }
  .contact .accent { color: var(--brand-blue); }
  .letter-body {
    position: absolute; left: 59px; top: 336px; width: 688px;
    font-size: 14.5px; line-height: 24.5px;
  }
  .salutation { font-weight: 700; color: var(--ink-dark); margin-bottom: 18px; }
  .letter-body p.para { margin-bottom: 18px; text-align: left; }
  .closing { position: absolute; left: 59px; top: 808px; font-size: 18px; color: var(--ink); }
  .signature {
    position: absolute; left: 59px; top: 840px;
    font-family: "Yellowtail", cursive; font-size: 32px; color: var(--brand-blue);
  }
  .footer-wave { position: absolute; left: 0; bottom: 0; width: 806px; height: 135px; }
  .footer-address {
    position: absolute; left: 0; right: 0; bottom: 14px;
    text-align: center; color: #fff; font-size: 11.5px; font-weight: 700;
    display: flex; justify-content: center; align-items: center; gap: 6px;
  }
  .footer-address svg { width: 10px; height: 10px; fill: #fff; }
</style>
</head>
<body>
  <main class="letterhead">
    <header>
      <div class="brand">
        <span class="brand-mark"></span>
        <span class="brand-name">MESA RIDGE SERVE</span>
      </div>
      <ul class="contact">
        <li><svg viewBox="0 0 24 24"><path d="M6.6 10.8a15 15 0 0 0 6.6 6.6l2.2-2.2c.3-.3.7-.4 1-.2 1.1.4 2.3.6 3.6.6.6 0 1 .4 1 1V20c0 .6-.4 1-1 1A17 17 0 0 1 3 4c0-.6.4-1 1-1h3.5c.6 0 1 .4 1 1 0 1.3.2 2.5.6 3.6.1.3 0 .7-.2 1z"/></svg>480 555 0142</li>
        <li><svg viewBox="0 0 24 24"><path d="M5 11l2-6h10l2 6h1v7h-2v2h-3v-2H9v2H6v-2H4v-7zm2.5 0h9l-1.2-4H8.7zM7 13.5a1.5 1.5 0 1 0 0 3 1.5 1.5 0 0 0 0-3zm10 0a1.5 1.5 0 1 0 0 3 1.5 1.5 0 0 0 0-3z"/></svg>480 555 0187</li>
        <li><svg viewBox="0 0 24 24"><path d="M2 5h20v14H2zm2 2v.5l8 5 8-5V7zm0 2.8V17h16V9.8l-8 5z"/></svg>Dana@<span class="accent">MesaRidgeServe</span>.com</li>
        <li><svg viewBox="0 0 24 24"><path d="M12 2a10 10 0 1 0 0 20 10 10 0 0 0 0-20zm6.9 6h-3a15 15 0 0 0-1.3-3.9A8 8 0 0 1 18.9 8zM12 4c.8 1.2 1.5 2.5 1.9 4h-3.8c.4-1.5 1.1-2.8 1.9-4zM4.3 14a8 8 0 0 1 0-4h3.4a16 16 0 0 0 0 4zm.8 2h3a15 15 0 0 0 1.3 3.9A8 8 0 0 1 5.1 16zm3-8h-3a8 8 0 0 1 4.3-3.9A15 15 0 0 0 8.1 8zM12 20c-.8-1.2-1.5-2.5-1.9-4h3.8c-.4 1.5-1.1 2.8-1.9 4zm2.3-6H9.7a14 14 0 0 1 0-4h4.6a14 14 0 0 1 0 4zm.3 5.9a15 15 0 0 0 1.3-3.9h3a8 8 0 0 1-4.3 3.9zm1.7-5.9a16 16 0 0 0 0-4h3.4a8 8 0 0 1 0 4z"/></svg><span class="accent">MesaRidgeServe.com</span></li>
      </ul>
    </header>

    <section class="letter-body">
      <p class="salutation">Dear Mr. Lorem,</p>
      <p class="para">Lorem ipsum dolor sit amet, consectetuer adipiscing elit, sed diam nonummy nibh euismod tincidunt ut laoreet dolore magna aliquam erat volutpat. Ut wisi enim ad minim veniam, quis nostrud exerci tation ullamcorper suscipit lobortis nisl ut aliquip ex ea commodo consequat. Duis autem vel eum iriure dolor in hendiusto odio dignissim qui blandit praesent luptatum zzril delenit augue duis dolore te feugait nulla facilisi.</p>
      <p class="para">Lorem ipsum dolor sit amet, consectetuer adipiscing elit, sed diam nonummy nibh euismod tincidunt ut laoreet dolore magna aliquam erat volutpat. Ut wisi enim ad minim veniam, quis nostrud exerci tation ullamcorper suscipit lobortis nisl ut aliquip ex ea commodo consequat. Duis autem vel eum iriure dolor in hendiusto odio dignissim qui blandit praesent luptatum zzril delenit augue duis dolore te feugait nulla facilisi.</p>
      <p class="para">Lorem ipsum dolor sit amet, consectetuer adipiscing elit, sed diam nonummy nibh euismod tincidunt ut laoreet dolore magna aliquam erat volutpat. Ut wisi enim ad minim veniam, quis nostrud exerci tation ullamcorper suscipit lobortis nisl ut aliquip ex ea commodo consequat. Duis autem vel eum iriure dolor in hendiusto odio dignissim qui blandit praesent luptatum zzril delenit augue duis dolore te feugait nulla facilisi.</p>
    </section>

    <p class="closing">Sincerely Your,</p>
    <p class="signature">Your Name</p>

    <footer>
      <svg class="footer-wave" viewBox="0 0 806 135" preserveAspectRatio="none">
        <path d="M0,0 C70,45 170,82 280,84 C450,86 620,20 806,6 L806,135 L0,135 Z" fill="var(--brand-blue)"/>
        <path d="M0,4 C70,48 170,84 280,86 C450,88 620,22 806,10" fill="none" stroke="#fff" stroke-width="5"/>
        <path d="M60,32 C140,68 220,84 300,80 C460,72 600,20 720,8 C600,28 460,86 300,92 C210,96 130,74 60,32 Z" fill="var(--swoosh)"/>
      </svg>
      <p class="footer-address"><svg viewBox="0 0 24 24"><path d="M12 2a7 7 0 0 0-7 7c0 5 7 13 7 13s7-8 7-13a7 7 0 0 0-7-7zm0 9.5a2.5 2.5 0 1 1 0-5 2.5 2.5 0 0 1 0 5z"/></svg>1420 E Canyon Rd STE 210, Tempe AZ 85281</p>
    </footer>
  </main>
</body>
</html>
```